Coastal Learner Bureau business cards

Australian company about to start offering its services. We recruit international students to come to study English, vocational education and postgraduate courses in Australia. We help them find the institution and select the right city they want to come to Australia. We are a young, online oriented and supportive agency. Our clients are between 18 and 35 years old, mainly University students, young professionals or people with work experience. We provide much more information that any other agency offer. We administrate a Facebook group with more than 11.000 members that daily ask questions about general information when coming to Australia, while they are here and even after they leave the country

Target Market(s)

International students from South America, Central America and Europe

Industry/Entity Type

Student

Contact Information for Business Card

Tomas Bilbrea
Managing Director
tomas@kelvarin.com.au
www.kelvoria.com.au
+61 491058264
Melbourne, Australia

Font styles to use
Serif
Sans Serif

Colors

Designer to choose colors to be used in the design.

Requirements
Must have
• Horizontal design
• Standard business card size and shape. If font uses green or yellow colours, they will have to match the ones from the logo
Nice to have
• UPDATE: Use the contents of the green image to design one of the card sides. Use our logo in the background of that side as watermark.
• Passport image, or immigration stamps. A picture of the Yarra River (from Melbourne) would be cool as well.
Should not have
• Non-standard business card size and shape
• Not black as the background colour of any sides as we are not a VIP agency or a hight class service. We are orientes to young people and they like colours, pictures, something attractive.
• Vertical design
• NO YELLOW or BLACK AS THE BACKGROUND COLOUR OF ANY SIDE OF THE BIZ CARD

```html
<!DOCTYPE html>
<html lang="en">
<head>
<meta charset="utf-8">
<title>Coastal Learner Bureau – Business Cards</title>
<link rel="stylesheet" href="https://fonts.googleapis.com/css2?family=Roboto:wght@400;500;700&family=Roboto+Condensed:wght@700&display=swap">
<style>
  :root {
    --backdrop: #2e2e2e;
    --card-white: #f2f2f2;
    --brand-green: #115c3c;
    --brand-yellow: #e0b416;
    --ink: #444444;
    --divider: #8a8a8a;
    --white: #ffffff;
  }
  html, body {
    margin: 0;
    padding: 0;
    width: 1200px;
    height: 960px;
    overflow: hidden;
    background: var(--backdrop);
    font-family: "Roboto", Arial, sans-serif;
  }
  .stage { position: relative; width: 1200px; height: 960px; }
  .card {
    position: absolute;
    width: 600px;
    height: 343px;
    overflow: hidden;
  }
  .card--front { left: 314px; top: 113px; background: var(--card-white); }
  .card--back  { left: 311px; top: 472px; background: var(--brand-green); }

  .brand-name {
    position: absolute;
    margin: 0;
    font-family: "Roboto", Arial, sans-serif;
    font-weight: 700;
    text-align: center;
    line-height: 1.05;
    letter-spacing: 0.5px;
  }
  .card--front .brand-name {
    left: 66px; top: 112px; width: 220px;
    font-size: 30px; color: var(--brand-green);
  }
  .brand-dot {
    position: absolute;
    width: 14px; height: 14px; border-radius: 50%;
    background: var(--brand-yellow);
  }
  .card--front .brand-dot { left: 170px; top: 222px; }

  .divider {
    position: absolute;
    left: 311px; top: 97px;
    width: 1px; height: 150px;
    background: linear-gradient(to bottom, transparent, var(--divider) 20%, var(--divider) 80%, transparent);
  }
  .contact { position: absolute; left: 344px; top: 110px; }
  .contact__name {
    margin: 0;
    font-family: "Roboto Condensed", "Arial Narrow", sans-serif;
    font-weight: 700; font-size: 21px; color: var(--brand-green);
    line-height: 24px; letter-spacing: 0.3px;
  }
  .contact__role {
    margin: 0;
    font-weight: 500; font-size: 15px; color: var(--brand-yellow);
    line-height: 20px; letter-spacing: 0.4px;
  }
  .contact__city {
    margin: 9px 0 10px;
    font-size: 14px; color: var(--ink); line-height: 18px;
  }
  .contact__line {
    display: flex; align-items: center; gap: 7px;
    font-size: 14px; color: var(--ink); line-height: 20px;
  }
  .contact__line svg { width: 13px; height: 13px; fill: var(--brand-green); }

  .band-yellow {
    position: absolute; left: 0; bottom: 0;
    width: 340px; height: 11px; background: var(--brand-yellow);
  }
  .band-green {
    position: absolute; right: 0; bottom: 0;
    width: 266px; height: 32px; background: var(--brand-green);
    clip-path: polygon(24px 0, 100% 0, 100% 100%, 0 100%);
  }
  .website {
    position: absolute; right: 0; bottom: 0;
    width: 266px; height: 32px; padding-left: 24px; box-sizing: border-box;
    display: flex; align-items: center; justify-content: center;
    font-size: 14px; color: var(--white); letter-spacing: 0.2px;
  }

  .card--back .brand-name {
    left: 150px; top: 115px; width: 300px;
    font-size: 40px; color: var(--white);
  }
  .card--back .brand-dot { left: 292px; top: 243px; width: 16px; height: 16px; }
  .tagline {
    position: absolute; left: 65px; top: 299px; width: 470px;
    display: flex; align-items: center; gap: 4px;
    font-size: 14px; color: var(--white);
  }
  .tagline::before, .tagline::after {
    content: ""; flex: 1; height: 1px;
  }
  .tagline::before { background: linear-gradient(to right, transparent, rgba(255,255,255,0.8)); }
  .tagline::after  { background: linear-gradient(to left, transparent, rgba(255,255,255,0.8)); }
</style>
</head>
<body>
<main class="stage">
  <section class="card card--front" aria-label="Business card front">
    <p class="brand-name">Coastal Learner Bureau</p>
    <span class="brand-dot"></span>
    <div class="divider"></div>
    <div class="contact">
      <h1 class="contact__name">TOMAS BILBREA</h1>
      <p class="contact__role">MANAGING DIRECTOR</p>
      <p class="contact__city">Melbourne, Australia</p>
      <div class="contact__line">
        <svg viewBox="0 0 24 24" aria-hidden="true"><path d="M6.6 10.8a15.1 15.1 0 0 0 6.6 6.6l2.2-2.2a1 1 0 0 1 1-.25 11.4 11.4 0 0 0 3.6.57 1 1 0 0 1 1 1V20a1 1 0 0 1-1 1A17 17 0 0 1 3 4a1 1 0 0 1 1-1h3.5a1 1 0 0 1 1 1c0 1.25.2 2.45.57 3.57a1 1 0 0 1-.25 1z"/></svg>
        <span>+61 491058264</span>
      </div>
      <div class="contact__line">
        <svg viewBox="0 0 24 24" aria-hidden="true"><path d="M2 5h20v2l-10 6L2 7z M2 9l10 6 10-6v10H2z"/></svg>
        <span>tomas@kelvarin.com.au</span>
      </div>
    </div>
    <div class="band-yellow"></div>
    <div class="band-green"></div>
    <div class="website">www.kelvoria.com.au</div>
  </section>

  <section class="card card--back" aria-label="Business card back">
    <p class="brand-name">Coastal Learner Bureau</p>
    <span class="brand-dot"></span>
    <p class="tagline">Hacemos más por ti!</p>
  </section>
</main>
</body>
</html>
```